Harborview Estates Business Card for Apartment Buildings

Create business cards for resident managers who run apartment buildings. The audience is the public who are searching for apartment rentals, and current residents who live at the apartment building. Key design element will be incorporating the company logo, however, the logo cannot dominate. The building name and manager name are more important than the logo. Current business card design leaves little room for copy, so we may need to reduce the size on the current card to allow for more space for copy.

Target Market(s)

Adults 18-65 years of age, who are looking for an apartment rental, plus current residents who live at our apartment buildings.

Industry/Entity Type

Property Management

Contact Information for Business Card

A major design element will be use of the company logo. Important property and manager contact information must be part of the design. The size of the logo will need to be reduced to make room for building and manager contact copy.

Font styles to use
Sans Serif

Colors
3176b5
000000
959595
ffffff

Requirements
Must have
• 1) Incorporate the company logo.
• 2) Use the company colors (dark blue, black/grey, over white).
• 3) FEATURE THE BUILDING NAME
• 4) FEATURE THE MANAGER NAME
• 5) The company name is less important than BUILDING and MANAGER
• 6) Manager contact information
• **SEE ATTACHED CREATIVE BRIEF**
Nice to have
• 1) Back of card logo watermark
• 2) Ability to write notes on back of carfd
Should not have
• Avoid letting the company logo dominate the card, the building name and manager are more important than the company logo.

```html
<!DOCTYPE html>
<html lang="en">
<head>
<meta charset="utf-8">
<title>Harborview Estates – Business Card</title>
<link href="https://fonts.googleapis.com/css2?family=Lato:wght@400;700;900&display=swap" rel="stylesheet">
<style>
  :root {
    --stage: #363636;
    --stage-light: #3f3f3f;
    --brand-blue: #1767ab;
    --ink: #2b2b2b;
    --rule: #d0d0d0;
    --paper: #ffffff;
  }
  * { margin: 0; padding: 0; box-sizing: border-box; }
  html, body { width: 1200px; height: 900px; overflow: hidden; }
  body {
    background: radial-gradient(ellipse at 50% 45%, var(--stage-light), var(--stage) 70%);
    font-family: "Lato", sans-serif;
    position: relative;
  }
  .card {
    position: absolute;
    top: 306px;
    width: 439px;
    height: 271px;
    background: var(--paper);
    box-shadow: 2px 3px 4px rgba(0,0,0,0.45);
    overflow: hidden;
  }
  .card--front { left: 149px; }
  .card--back { left: 608px; }

  .brand {
    position: absolute;
    left: 30px;
    top: 62px;
    width: 142px;
    text-align: center;
  }
  .brand__dot {
    width: 62px; height: 62px;
    margin: 0 auto 14px;
    border-radius: 50%;
    background: var(--brand-blue);
  }
  .brand__name {
    font-weight: 900;
    color: var(--brand-blue);
    font-size: 19px;
    line-height: 1.05;
    text-transform: uppercase;
    letter-spacing: 0.3px;
  }

  .divider {
    position: absolute;
    left: 191px;
    top: 62px;
    width: 1px;
    height: 145px;
    background: linear-gradient(to bottom, transparent, var(--rule) 20%, var(--rule) 80%, transparent);
  }

  .details {
    position: absolute;
    left: 217px;
    top: 61px;
    color: var(--ink);
  }
  .details__name {
    font-weight: 700;
    font-size: 19.5px;
    color: var(--brand-blue);
    letter-spacing: 0.2px;
    line-height: 1.1;
  }
  .details__title { font-size: 12px; margin-top: 1px; }
  .contact-list { list-style: none; margin-top: 14px; }
  .contact-list li {
    font-size: 12px;
    line-height: 15.8px;
    display: flex;
    align-items: center;
    gap: 5px;
  }
  .contact-list svg { width: 10px; height: 10px; fill: var(--brand-blue); flex: none; }
  .address { font-size: 12px; line-height: 15.5px; margin-top: 9px; }

  .back-band {
    position: absolute;
    left: 0;
    width: 100%;
    background: var(--brand-blue);
  }
  .back-band--top { top: 0; height: 80px; }
  .back-band--bottom { top: 194px; height: 77px; }
  .notes-area {
    position: absolute;
    left: 0; top: 80px;
    width: 100%; height: 114px;
    background: var(--paper);
  }
</style>
</head>
<body>
  <section class="card card--front" aria-label="Business card front">
    <div class="brand">
      <div class="brand__dot"></div>
      <div class="brand__name">Harborview Estates</div>
    </div>

    <div class="divider"></div>

    <div class="details">
      <h1 class="details__name">DANIEL WHITAKER</h1>
      <p class="details__title">Property Manager</p>
      <ul class="contact-list">
        <li>
          <svg viewBox="0 0 10 10" aria-hidden="true"><path d="M1 3.2C1 2 2.5 1.5 5 1.5S9 2 9 3.2L7.4 3.8 6.8 2.9H3.2L2.6 3.8ZM2.3 4.5H7.7L8.8 8.5H1.2Z"/></svg>
          555-214-7730
        </li>
        <li>
          <svg viewBox="0 0 10 10" aria-hidden="true"><path d="M2.5 1H7.5V3.2H2.5ZM1 3.8H9V7.5H7.5V6H2.5V7.5H1ZM3 6.5H7V9.2H3Z"/></svg>
          555-214-7731
        </li>
        <li>
          <svg viewBox="0 0 10 10" aria-hidden="true"><path d="M1 2.5H9V3.2L5 5.8 1 3.2ZM1 4.2L5 6.8 9 4.2V7.8H1Z"/></svg>
          daniel@harborviewestates.us
        </li>
        <li>
          <svg viewBox="0 0 10 10" aria-hidden="true"><circle cx="5" cy="5" r="4.2"/></svg>
          www.harborviewestates.us
        </li>
      </ul>
      <p class="address">1280 Bayside Crest Road #B210<br>Portside, CA 90410</p>
    </div>
  </section>

  <section class="card card--back" aria-label="Business card back">
    <div class="back-band back-band--top" role="img" aria-label="Repeating company mark watermark pattern"></div>
    <div class="notes-area" aria-label="Space for notes"></div>
    <div class="back-band back-band--bottom" role="img" aria-label="Repeating company mark watermark pattern"></div>
  </section>
</body>
</html>
```